Recruitment of Trellan Staffing for the UK market

I want a website for the UK market to attract businesses and companies to come to us for Philipine labour. We want an information site that gives all information on what we do and how we can recruit Philippine labour.
This is a recruitment site for companies to contact us with their requirements for skilled workers coming from the Philipines over to the UK to work.

Target Market(s)

Uk Companies and businesses who want Philipine skilled workers

Industry/Entity Type

REcruitment

Coding

Number of Pages Required

5+ page

Font styles to use
Sans Serif

Colors
0054AA
0677BA
7BADD7
CADEEF
E8F1F8
0094D4
00A9DD
6FCCEA
C7EBF8
E9F6FB
EE7325
F08F49
F5BC92
FAE3D3
FDF4ED
EB3D1F
EC4F4E
F09395
F8D3D4
FCEDEE

Requirements
Must have
• Look professional and corperate with drop down menus for Home ,about, services,articles. training , contact us
Nice to have
• Look at Velmora recruitment- https://velmorarecruitment.example.co.uk/. This is my current site - https://www.trellanstaffing.example.com/
Should not have
• Cartoons or silly pictures , needs to be corperate looking

```html
<!DOCTYPE html>
<html lang="en">
<head>
<meta charset="utf-8">
<title>Trellan Staffing – Skilled Philippine Workers for UK Companies</title>
<link rel="stylesheet" href="https://fonts.googleapis.com/css2?family=Poppins:wght@400;500;600;700&display=swap">
<style>
:root{
  --blue-dark:#0054AA;
  --blue:#0677BA;
  --sky:#00A9DD;
  --sky-mid:#0094D4;
  --orange:#EE7325;
  --orange-light:#F08F49;
  --cream:#FDF4ED;
  --brand:#9B2F2F;
  --text:#333;
  --white:#fff;
}
*{box-sizing:border-box;margin:0;padding:0}
html,body{width:1200px;height:3919px;overflow:hidden}
body{font-family:"Poppins",sans-serif;color:var(--text);background:var(--white);position:relative}
.abs{position:absolute}
a{color:inherit;text-decoration:none}

/* header */
.site-header{left:0;top:0;width:1200px;height:96px;background:var(--white)}
.brand{display:flex;align-items:center;gap:10px;font-weight:700;font-size:26px;color:var(--brand)}
.brand-dot{width:14px;height:14px;background:var(--brand);border-radius:50%}
.site-header .brand{left:75px;top:28px}
.main-nav{right:74px;top:40px;display:flex;gap:44px;font-size:16px;font-weight:500;color:#222}
.main-nav .active{color:var(--blue-dark)}

/* hero */
.hero{left:0;top:96px;width:1200px;height:683px;background:linear-gradient(110deg,#3a3f33 0%,#6b6a3c 35%,#8d8848 55%,#4b5048 80%,#2f3436 100%)}
.hero-title{left:75px;top:300px;width:640px;font-size:44px;line-height:58px;font-weight:700;color:var(--white)}
.btn-orange{left:75px;top:500px;width:179px;height:61px;background:var(--orange);color:var(--white);font-weight:600;font-size:17px;display:flex;align-items:center;justify-content:center;border-radius:2px}
.contact-box{left:794px;top:183px;width:331px;height:511px;background:rgba(255,255,255,.92);padding:16px 20px}
.contact-box h2{font-size:45px;line-height:46px;font-weight:600;color:#333;margin-bottom:22px}
.field{width:292px;height:50px;border:1px solid #ccc;background:var(--white);margin-bottom:13px;font-size:15px;padding:14px 15px;color:#222}
.field.msg{height:110px}
.btn-submit{width:292px;height:50px;background:var(--blue-dark);color:var(--white);font-weight:600;font-size:18px;display:flex;align-items:center;justify-content:center;border-radius:2px}

/* about */
.photo{border:0}
.ph-team{left:75px;top:827px;width:389px;height:324px;background:linear-gradient(135deg,#6f7780,#c9c3bf 50%,#8a8e92)}
.ph-map{left:260px;top:989px;width:321px;height:345px;background:linear-gradient(160deg,#8ab4f2,#7faaee 60%,#a9c79a)}
.ph-staff{left:122px;top:1088px;width:194px;height:174px;background:linear-gradient(135deg,#6a8fb3,#4f7fb0 60%,#9eb4c8);border:7px solid var(--white)}
.section-h{color:var(--blue-dark);font-weight:500}
.about-h{left:616px;top:918px;font-size:50px;line-height:53px}
.body-copy{font-size:17px;line-height:34px;color:#444}
.about-copy{left:616px;top:1050px;width:520px}

.team-h{left:76px;top:1480px;font-size:36px;line-height:52px;width:900px}

/* service cards */
.card{top:1627px;width:252px;height:366px;color:var(--white);padding:26px 22px}
.card svg{width:68px;height:68px;display:block;margin-bottom:14px}
.card h3{font-size:24px;font-weight:600;margin-bottom:8px}
.card p{font-size:15px;line-height:26.6px;height:186px}
.card .more{font-size:15px;font-weight:600}
.c1{left:75px;background:var(--sky)}
.c2{left:341px;background:var(--sky-mid)}
.c3{left:607px;background:var(--orange)}
.c4{left:875px;background:var(--orange-light)}

/* feature rows */
.feature-box{background:var(--white);padding:36px 22px}
.feature-box h2{font-size:48px;line-height:60px;color:var(--blue-dark);font-weight:500;margin-bottom:14px;white-space:nowrap}
.link-orange{color:var(--orange);font-weight:600;font-size:18px;text-decoration:underline;text-underline-offset:5px;display:inline-block;margin-top:24px}
.ph-workers{left:75px;top:2103px;width:512px;height:440px;background:linear-gradient(135deg,#c9cfd6,#5a6f8c 45%,#2f4064)}
.ph-nurse{left:613px;top:2589px;width:513px;height:438px;background:linear-gradient(135deg,#d7cbb6,#bfcfdc 50%,#3d82c1)}
.ph-warehouse{left:75px;top:3075px;width:512px;height:440px;background:linear-gradient(135deg,#e9e4dc,#b89a6a 45%,#3a3c44)}
.fb1{left:509px;top:2154px;width:617px;height:337px}
.fb2{left:52px;top:2640px;width:639px;height:335px;padding-left:22px}
.fb3{left:509px;top:3127px;width:617px;height:336px}

/* footer */
.site-footer{left:0;top:3594px;width:1200px;height:325px;background:var(--cream)}
.site-footer .brand{left:75px;top:3700px;font-size:22px}
.legal{left:76px;top:3772px;font-size:14px;line-height:29px;color:#555}
.foot-h{font-size:20px;font-weight:600;color:var(--blue-dark)}
.foot-list{list-style:none;font-size:15px;line-height:33px;color:#222}
.col-map{left:356px;top:3640px}
.col-contact{left:564px;top:3640px}
.col-follow{left:919px;top:3640px}
.info-row{display:flex;gap:14px;font-size:15px;line-height:26px;color:#222;margin-top:6px}
.info-row svg{width:20px;height:20px;flex:none;margin-top:3px}
.socials{display:flex;gap:20px;margin-top:26px}
.social{width:24px;height:24px;border-radius:50%;background:#333}
</style>
</head>
<body>

<header class="site-header abs">
  <div class="brand abs"><span class="brand-dot"></span>Trellan Staffing</div>
  <nav class="main-nav abs">
    <a class="active" href="#">Home</a><a href="#">About</a><a href="#">Services</a><a href="#">Articles</a><a href="#">Training</a><a href="#">Contact Us</a>
  </nav>
</header>

<section class="hero abs" role="img" aria-label="Photo of two engineers in hard hats and hi-vis vests on a site"></section>
<h1 class="hero-title abs">Recruiting and placing skilled Philippine workers into UK companies</h1>
<a class="btn-orange abs" href="#">Learn More</a>
<form class="contact-box abs">
  <h2>Contact Us Today</h2>
  <div class="field">Name</div>
  <div class="field">Email Address</div>
  <div class="field">Phone</div>
  <div class="field msg">Message</div>
  <div class="btn-submit">Submit</div>
</form>

<div class="photo ph-team abs" role="img" aria-label="Photo of a smiling team of office workers"></div>
<div class="photo ph-map abs" role="img" aria-label="Map of the Philippines with office locations"></div>
<div class="photo ph-staff abs" role="img" aria-label="Photo of medical staff in blue uniforms"></div>
<h2 class="section-h about-h abs">What the business<br>is about</h2>
<p class="body-copy about-copy abs">We source skilled workers directly from the Philippines to work in the UK. With offices , training locations and specialist recruiters we can find the highest quality individuals to add value and resources to any UK buisness. We delivery quality based on vast experience over a number of years.</p>

<h2 class="section-h team-h abs">We recruit the finest talent available with our dedicated 200 strong team.</h2>

<article class="card c1 abs">
  <svg viewBox="0 0 68 68" fill="none" stroke="#fff" stroke-width="2"><circle cx="22" cy="22" r="8"/><path d="M8 50l14-14 12 10M30 40l20-18M44 14l8 8M50 10l6 6M12 58h44"/></svg>
  <h3>What we do</h3>
  <p>Our company has been estabilished in the Philippines for over 20 years. We have mainly been recruiting philippine workers for the off shore.</p>
  <a class="more" href="#">Read More &#8250;</a>
</article>
<article class="card c2 abs">
  <svg viewBox="0 0 68 68" fill="none" stroke="#fff" stroke-width="2"><circle cx="34" cy="20" r="7"/><circle cx="16" cy="30" r="6"/><circle cx="52" cy="30" r="6"/><path d="M22 58V38h24v20M6 58V44h16M46 44h16v14"/></svg>
  <h3>How we help</h3>
  <p>We work with companies to find skilled workers that meet the UK requirements for Visas and work permits. We guide you through the whole process.</p>
  <a class="more" href="#">Read More &#8250;</a>
</article>
<article class="card c3 abs">
  <svg viewBox="0 0 68 68" fill="none" stroke="#fff" stroke-width="2"><path d="M58 10C40 10 28 22 22 38l8 8c16-6 28-18 28-36z"/><circle cx="42" cy="26" r="5"/><path d="M22 38l-10 2 8-12M30 46l-2 10 12-8M18 50l-8 8"/></svg>
  <h3>Where to start</h3>
  <p>We need to know what your issues are and how we can understand the personnal you require , over what time frame and the number.</p>
  <a class="more" href="#">Read More &#8250;</a>
</article>
<article class="card c4 abs">
  <svg viewBox="0 0 68 68" fill="none" stroke="#fff" stroke-width="2"><path d="M14 10l10 10-6 8c4 8 10 14 18 18l8-6 10 10-8 8C26 56 10 40 6 18z"/><rect x="30" y="18" width="32" height="22"/><path d="M30 18l16 12 16-12"/></svg>
  <h3>Contact us today</h3>
  <p>Please contact us today with your requirements , this can be care workers ,chef, welders, pipe fitters, caravan cabinet makers, medical workers.</p>
  <a class="more" href="#">Read More &#8250;</a>
</article>

<div class="photo ph-workers abs" role="img" aria-label="Photo of engineers in hard hats inspecting machinery"></div>
<div class="feature-box fb1 abs">
  <h2>UK Skilled Workers List</h2>
  <p class="body-copy">The UK government since brexit have developed a new system based on points (similar to Australia) when recruiting from outside of the UK. Previuosly EU citizens could work in the UK without any extensive ducumentation or clarification of skills.</p>
  <a class="link-orange" href="#">View Listing</a>
</div>

<div class="photo ph-nurse abs" role="img" aria-label="Photo of a smiling nurse in blue scrubs"></div>
<div class="feature-box fb2 abs">
  <h2>Sponsor Licence</h2>
  <p class="body-copy">If you have areas of your business that meet the entry requirements of skilled labour your next step is to gain a sponsor licence for your business. There are different types of licences depending on the size of the business.</p>
  <a class="link-orange" href="#">Read More</a>
</div>

<div class="photo ph-warehouse abs" role="img" aria-label="Photo of warehouse workers at a desk with a laptop"></div>
<div class="feature-box fb3 abs">
  <h2>Recruitment Timeline</h2>
  <p class="body-copy">The UK government since brexit have developed a new system based on points (similar to Australia) when recruiting from outside of the UK. Previuosly EU citizens could work in the UK without any extensive ducumentation or clarification of skills.</p>
  <a class="link-orange" href="#">View Listing</a>
</div>

<footer class="site-footer abs"></footer>
<div class="brand abs site-footer-brand" style="left:75px;top:3700px;font-size:22px"><span class="brand-dot"></span>Trellan Staffing</div>
<p class="legal abs">© 2023 Trellan Staffing<br>All Rights Reserved.</p>

<div class="col-map abs">
  <h4 class="foot-h">Site Map</h4>
  <ul class="foot-list"><li>Home</li><li>About</li><li>Services</li><li>Articles</li><li>Training</li><li>Contact Us</li></ul>
</div>

<div class="col-contact abs">
  <h4 class="foot-h">Contact Info</h4>
  <div class="info-row"><svg viewBox="0 0 20 20" fill="#EE7325"><path d="M2 4l5-2 6 2 5-2v14l-5 2-6-2-5 2z"/></svg><span>Larkspur Gardens,<br>Elmwick EW4 2<br>United Kingdom</span></div>
  <div class="info-row"><svg viewBox="0 0 20 20" fill="#EE7325"><path d="M4 2l4 4-2 3c1 2 3 4 5 5l3-2 4 4-3 3C8 18 2 12 1 5z"/></svg><span>07700900412</span></div>
  <div class="info-row"><svg viewBox="0 0 20 20" fill="#EE7325"><rect x="1" y="4" width="18" height="12"/><path d="M1 4l9 7 9-7" stroke="#fff" stroke-width="1.5" fill="none"/></svg><span>sales@trellanstaffing.example.com</span></div>
</div>

<div class="col-follow abs">
  <h4 class="foot-h">Follow Us</h4>
  <div class="socials">
    <span class="social" role="img" aria-label="Social profile"></span>
    <span class="social" role="img" aria-label="Social profile"></span>
    <span class="social" role="img" aria-label="Social profile"></span>
    <span class="social" role="img" aria-label="Social profile"></span>
    <span class="social" role="img" aria-label="Video channel"></span>
  </div>
</div>

</body>
</html>
```